Medical Practice needs a Letterhead Design

We need a clean, modern letterhead design for our stem cell medical practice.

Industry/Entity Type

Medical

```html
<!DOCTYPE html>
<html lang="en">
<head>
<meta charset="utf-8">
<title>Vitacore Clinic Letterhead</title>
<link rel="stylesheet" href="https://fonts.googleapis.com/css2?family=Lato:wght@400;700&family=Tinos&display=swap">
<style>
  :root {
    --backdrop: #e3d8c3;
    --paper: #ffffff;
    --navy: #1d3447;
    --leaf: #a9c23f;
    --ink: #1c1c1c;
    --rule: #2a2a2a;
    --muted: #6e7378;
  }
  * { box-sizing: border-box; margin: 0; padding: 0; }
  html, body {
    width: 1200px;
    height: 1000px;
    overflow: hidden;
    background: var(--backdrop);
  }
  .letterhead {
    position: absolute;
    left: 268px;
    top: 30px;
    width: 664px;
    height: 940px;
    background: var(--paper);
    box-shadow: 0 6px 24px rgba(90, 70, 40, 0.18);
  }
  .brand {
    position: absolute;
    top: 110px;
    left: 0;
    width: 100%;
    display: flex;
    justify-content: center;
    align-items: center;
    gap: 10px;
  }
  .brand-dot {
    width: 12px;
    height: 12px;
    border-radius: 50%;
    background: var(--leaf);
  }
  .brand-name {
    font-family: "Lato", sans-serif;
    font-weight: 700;
    font-size: 34px;
    color: var(--navy);
    letter-spacing: 0.5px;
  }
  .rule {
    position: absolute;
    height: 1px;
    background: var(--rule);
  }
  .rule-header { top: 215px; left: 60px; right: 60px; }
  .rule-accent { top: 790px; left: 440px; right: 48px; }
  .rule-footer { top: 860px; left: 210px; right: 48px; }
  .letter {
    position: absolute;
    top: 262px;
    left: 92px;
    width: 470px;
    font-family: "Tinos", serif;
    font-size: 12.5px;
    line-height: 1.32;
    color: var(--ink);
  }
  .letter-date { margin-bottom: 18px; }
  .letter-recipient { margin-left: 10px; margin-bottom: 16px; }
  .letter-body { margin-left: 22px; text-align: justify; }
  .letter-closing { margin-left: 22px; margin-top: 30px; }
  .letter-signature { margin-left: 22px; margin-top: 18px; }
  .contact {
    position: absolute;
    top: 878px;
    left: 300px;
    display: flex;
    gap: 44px;
    font-family: "Lato", sans-serif;
    font-size: 8.5px;
    color: var(--muted);
  }
  .contact-column { display: flex; flex-direction: column; gap: 6px; }
  .contact-item { display: flex; align-items: center; gap: 7px; }
  .contact-icon { width: 11px; height: 11px; flex: none; }
</style>
</head>
<body>
  <main class="letterhead">
    <header class="brand">
      <span class="brand-dot"></span>
      <span class="brand-name">Vitacore Clinic</span>
    </header>
    <div class="rule rule-header"></div>

    <article class="letter">
      <p class="letter-date">April 28. 2014</p>
      <p class="letter-recipient">Daniel Reed,<br>1234 Street Ave,<br>Somewhere.</p>
      <p class="letter-body">Dear Ms Reed,<br>
      Lorem ipsum dolor sit amet, consectetur adipiscing elit. Vestibulum sollicitudin rhoncus molestie. Etiam sed libero ultricies, cursus nisl at, scelerisque diam. Aliquam erat volutpat. Phasellus vel dignissim eros. Nullam eu lorem fermentum, porta magna a, sodales massa. Lorem ipsum dolor sit amet, consectetur adipiscing elit. Duis mollis, tortor sit amet mattis suscipit, nulla quam dictum enim, at maximus sapien ante vitae massa. Maecenas molestie neque vel purus fringilla, id consectetur sapien volutpat. Sed imperdiet bibendum tellus, a feugiat diam finibus nec. Lorem ipsum dolor sit amet, consectetur adipiscing elit. Pellentesque blandit quam vitae nibh mattis, in euismod mi tempor. Aenean pulvinar scelerisque turpis, fermentum pharetra arcu commodo quis. Donec vitae orci pulvinar, faucibus felis id, gravida dolor. Morbi at faucibus ante, dictum varius elit. Nulla purus eros, cursus sit amet scelerisque a, condimentum aliquam est. Nulla sed nulla sagittis, tempor massa non, volutpat libero. Quisque sed semper elit, vitae mattis dolor. Fusce tellus orci, mattis eu orci sed, facilisis sollicitudin velit. In porttitor lectus velit, eget auctor augue euismod quis. Suspendisse in libero ut nunc ultricies posuere non ac ipsum. Fusce consequat elementum turpis, eu feugiat purus molestie lacinia.</p>
      <p class="letter-closing">Sincerely</p>
      <p class="letter-signature">Mr. Reed</p>
    </article>

    <div class="rule rule-accent"></div>
    <div class="rule rule-footer"></div>

    <footer class="contact">
      <div class="contact-column">
        <div class="contact-item">
          <svg class="contact-icon" viewBox="0 0 12 12" aria-hidden="true"><path d="M6 0.5a3.8 3.8 0 0 0-3.8 3.8C2.2 7 6 11.5 6 11.5S9.8 7 9.8 4.3A3.8 3.8 0 0 0 6 0.5z" fill="#222"/><circle cx="6" cy="4.3" r="1.4" fill="#fff"/></svg>
          <span>Address: To be confirmed</span>
        </div>
        <div class="contact-item">
          <svg class="contact-icon" viewBox="0 0 12 12" aria-hidden="true"><rect x="3" y="0.5" width="6" height="11" rx="1.2" fill="none" stroke="#222" stroke-width="1.2"/><circle cx="6" cy="9.5" r="0.7" fill="#222"/></svg>
          <span>Phone: To be confirmed</span>
        </div>
      </div>
      <div class="contact-column">
        <div class="contact-item">
          <svg class="contact-icon" viewBox="0 0 12 12" aria-hidden="true"><rect x="0.5" y="4" width="11" height="7" rx="1" fill="#222"/><rect x="3" y="0.8" width="6" height="4" fill="none" stroke="#222" stroke-width="1"/><rect x="3" y="6" width="6" height="1" fill="#fff"/></svg>
          <span>Fax: To be confirmed</span>
        </div>
        <div class="contact-item">
          <svg class="contact-icon" viewBox="0 0 12 12" aria-hidden="true"><rect x="0.5" y="2.5" width="11" height="7.5" fill="#222"/><path d="M0.8 2.8 6 7l5.2-4.2" fill="none" stroke="#fff" stroke-width="0.9"/></svg>
          <span>Email: hello@vitacoreclinic.com</span>
        </div>
      </div>
    </footer>
  </main>
</body>
</html>
```